Wordpress Design Project

We are an online jewellery business currently trading entirely online through internet auctions.

We are revamping our online operations. We want to launch our website. Which will incorporate extensive social media integration. Chatterloop, Blogging to chatterloop as well as Boardquill. These need to be linked (some and/or interactive).

We want to collect subscriptions and collate emails/info.

There may also be video uploads of our stock.

Whilst we are Sydney based we see ourselves as a global business.

We sell High End exclusive designer jewellery.
Often bespoke pieces of diamond jewellery.

Words that some up our brand personality
Savvy, Stylish, Confident, Approachable

About our style
Ensuring not only that our designs and jewellery have a certain sense of classic or fashion-driven style, but expressing style and beauty through all touch points. We understand that style is not only about what you wear, but how you carry yourself.

About our company mission
Make precious jewellery an affordable luxury for stylish, savvy buyers
Create products that we're proud to sell and that customers desire, treasure and proudly wear.

KEY FOCUS/OUTCOME:

We require a stylish, clean, visually easy to navigate website. Main aim of the site is to showcase products. Not a shop per se. Ultimate goal is to engage the viewer to ask us to make something special for them. Not a huge budget. WE are a small business. But we make beautiful fine jewellery. Focus on Blog, social media interactions important, Innovative WORDPRESS design. Think special. We want to be inspired as we are inspired by some of the links we've presented here. They give a great overall feel of what we are looking for.

We require full implementation to be delivered.

http://www.tarvoselk.com/
http://www.merovatrikes.com/
http://www.fenwardspirit.com/cocktails/
www.plomarn.ch
http://www.vuralette.fr/en

SEO expertise as well as adaptation across all mobile devices/tablets.

Requirements
Must have
• Social Media, Blog, unique design (not same-same) Has to feel bespoke. 48 hour "buy it now" feature. Like a daily deal function with the ability to check out through CoinVeil. One high ticket item per day. Easy for us to manipulate/upload to website. User friendly.
Fast website. Not slow.
Should not have
• -should not look like a traditional shopping cart.

```html
<!DOCTYPE html>
<html lang="en">
<head>
<meta charset="utf-8">
<title>Verantelli | Designer Jewellery</title>
<link href="https://fonts.googleapis.com/css2?family=Lobster&family=Roboto:wght@400;500;700&display=swap" rel="stylesheet">
<style>
:root{
  --gold:#dcaa5c;
  --ink:#000000;
  --header-bg:#0b0c0e;
  --nav-bg:#111215;
  --footer-bg:#0e0f11;
  --rule:#24262a;
  --nav-text:#9b9b9b;
  --footer-text:#6a6a6a;
  --white:#ffffff;
  --teal:#3fc9c6;
}
*{margin:0;padding:0;box-sizing:border-box}
html,body{width:1200px;height:780px;overflow:hidden;background:var(--ink)}
body{font-family:"Roboto",Arial,sans-serif;position:relative}
.page{position:relative;width:1200px;height:780px;border-top:4px solid var(--gold);border-bottom:4px solid var(--gold);background:var(--ink)}

.site-header{position:absolute;left:0;top:0;width:1200px;height:106px;background:var(--header-bg);border-bottom:1px solid var(--rule)}
.brand{position:absolute;left:0;width:1200px;top:30px;text-align:center;color:var(--white)}
.brand-name{display:block;font-size:31px;font-weight:400;letter-spacing:1px;line-height:34px}
.brand-tagline{display:block;font-size:11px;margin-top:6px;padding-left:96px;letter-spacing:.2px}

.main-nav{position:absolute;left:0;top:107px;width:1200px;height:45px;background:var(--nav-bg)}
.main-nav ul{list-style:none;position:absolute;left:120px;top:10px;display:flex;height:30px}
.main-nav li{font-size:12.5px;font-weight:500;color:var(--nav-text);text-transform:uppercase;line-height:30px;padding:0 16px;border-right:1px solid var(--rule)}
.main-nav li.active{color:var(--gold)}
.main-nav li.bag{border-right:none;color:var(--gold);font-weight:700;display:flex;align-items:center;gap:6px;padding-left:12px}
.main-nav li.bag .count{color:var(--nav-text);font-weight:400}

.hero{position:absolute;left:0;top:152px;width:1200px;height:500px;background:var(--ink)}
.hero-photo{position:absolute;left:165px;top:0;width:385px;height:432px;background:radial-gradient(ellipse at 45% 60%,#d9dcda 0%,#9a9b94 22%,#5a4a2e 42%,#1a1610 62%,#000 80%)}
.hero-title{position:absolute;left:573px;top:180px;color:var(--gold);font-family:"Lobster",cursive;font-size:60px;font-weight:400;line-height:70px}
.hero-subtitle{position:absolute;left:573px;top:245px;color:var(--white);font-size:36px;font-weight:400;letter-spacing:1px;line-height:42px}
.slider-pager{position:absolute;left:0;top:446px}

.site-footer{position:absolute;left:0;top:652px;width:1200px;height:124px;background:var(--footer-bg)}
.footer-links{position:absolute;top:8px;list-style:none}
.footer-links li{font-size:12.5px;color:var(--footer-text);line-height:20px}
.footer-links.col-a{left:120px}
.footer-links.col-b{left:359px}
.mailing{position:absolute;left:579px;top:8px}
.mailing-label{font-size:12px;color:var(--footer-text);text-transform:uppercase;line-height:16px}
.mailing-input{position:absolute;left:1px;top:26px;width:240px;height:30px;background:#030304;border:none}
.mailing-button{position:absolute;left:171px;top:62px;width:70px;height:30px;background:var(--gold);color:#1a1408;font-weight:700;font-size:14px;border:none;font-family:inherit;letter-spacing:.3px}
.social{position:absolute;left:910px;top:21px;display:flex;gap:4px;list-style:none}
.social li{width:31px;height:31px;border-radius:50%;background:var(--gold)}
.copyright{position:absolute;right:122px;top:74px;font-size:12px;color:var(--footer-text)}
</style>
</head>
<body>
<div class="page">
  <header class="site-header">
    <div class="brand">
      <span class="brand-name">VERANTELLI</span>
      <span class="brand-tagline">designer jewellery</span>
    </div>
  </header>

  <nav class="main-nav">
    <ul>
      <li class="active">Collections</li>
      <li>About Us</li>
      <li>Blog</li>
      <li>Education</li>
      <li>Buying From Us</li>
      <li>Testimonials</li>
      <li>48 Hour Product Offer</li>
      <li class="bag">
        <svg width="19" height="16" viewBox="0 0 19 16" aria-hidden="true">
          <path d="M1 1.5h3l2.2 9h9.3l2-6.5H5" fill="none" stroke="#dcaa5c" stroke-width="1.6" stroke-linejoin="round"/>
          <path d="M7 5.5h9M7.6 8h7.8" stroke="#dcaa5c" stroke-width="1.2"/>
          <circle cx="7.5" cy="14" r="1.4" fill="#dcaa5c"/>
          <circle cx="14.5" cy="14" r="1.4" fill="#dcaa5c"/>
        </svg>
        <span>Shopping Bag<span class="count">: 0</span></span>
      </li>
    </ul>
  </nav>

  <section class="hero">
    <div class="hero-photo" role="img" aria-label="Pair of yellow gold pendants set with white pearls and baguette diamonds on black"></div>
    <h1 class="hero-title">Yellow Gold Pearl</h1>
    <h2 class="hero-subtitle">DIAMOND PENDANT</h2>
    <svg class="slider-pager" width="1200" height="20" viewBox="0 0 1200 20" aria-label="Slide 2 of 4">
      <defs>
        <linearGradient id="rule-left" x1="0" x2="1">
          <stop offset="0" stop-color="#2e2f33" stop-opacity="0"/>
          <stop offset="1" stop-color="#3a3b3f"/>
        </linearGradient>
        <linearGradient id="rule-right" x1="0" x2="1">
          <stop offset="0" stop-color="#3a3b3f"/>
          <stop offset="1" stop-color="#2e2f33" stop-opacity="0"/>
        </linearGradient>
      </defs>
      <rect x="262" y="9.5" width="216" height="1" fill="url(#rule-left)"/>
      <rect x="568" y="9.5" width="222" height="1" fill="url(#rule-right)"/>
      <circle cx="497" cy="10" r="5" fill="#3a3b3e" stroke="#55565a"/>
      <circle cx="515" cy="10" r="5.5" fill="#4a4b4e" stroke="#3fc9c6" stroke-width="2"/>
      <circle cx="533" cy="10" r="5" fill="#3a3b3e" stroke="#55565a"/>
      <circle cx="551" cy="10" r="5" fill="#3a3b3e" stroke="#55565a"/>
    </svg>
  </section>

  <footer class="site-footer">
    <ul class="footer-links col-a">
      <li>Customer Care</li>
      <li>Product Information</li>
      <li>Shipping &amp; Delivery</li>
      <li>Returns &amp; Exchanges</li>
      <li>Privacy &amp; Security</li>
    </ul>
    <ul class="footer-links col-b">
      <li>Faq</li>
      <li>Contact us</li>
      <li>Terms &amp; Conditions</li>
      <li>Site Map</li>
    </ul>
    <form class="mailing">
      <p class="mailing-label">Join our mailing list</p>
      <input class="mailing-input" type="email" aria-label="Email address">
      <button class="mailing-button" type="button">SIGN IN</button>
    </form>
    <ul class="social" aria-label="Social channels">
      <li aria-label="Chatterloop"></li>
      <li aria-label="Social channel"></li>
      <li aria-label="Social channel"></li>
      <li aria-label="Boardquill"></li>
      <li aria-label="News feed"></li>
    </ul>
    <p class="copyright">© 2013 Verantelli | Designer Jewellery</p>
  </footer>
</div>
</body>
</html>
```